you will use Ai to Copy the website Brivanta.com to come up with the basic frame work and it will give you the understanding of how I would like Kelbrava.com to be like. Kelbrava.com is a peer to peer rv rental site very similar to both of the other rv rental sites the difference is that are commission based 20% and above per rental and we will be one flat monthly rate and they keep all the earnings. Below is photo that will help you with the color scheme and the look and feel of the design

1 page

```html
<!DOCTYPE html>
<html lang="en">
<head>
<meta charset="utf-8">
<title>Kelbrava.com – The Smart Way to Rent an RV</title>
<link href="https://fonts.googleapis.com/css2?family=Figtree:wght@400;500;600;700;800&display=swap" rel="stylesheet">
<style>
:root{
  --navy:#0f1e3a;
  --navy-deep:#0b1830;
  --green:#4b7d22;
  --green-dark:#3d6a1a;
  --ink:#15223b;
  --muted:#5d6675;
  --soft:#8a919c;
  --line:#e3e6ea;
  --tint:#eef3ef;
  --white:#ffffff;
  --star:#f0a020;
}
*{box-sizing:border-box;margin:0;padding:0}
html,body{width:1200px;height:2966px;overflow:hidden}
body{font-family:"Figtree",Arial,sans-serif;color:var(--ink);background:var(--white)}
a{color:inherit;text-decoration:none}
.btn{display:inline-flex;align-items:center;justify-content:center;background:var(--green);color:var(--white);font-weight:600;font-size:13px;border-radius:3px}

/* Header */
.site-header{height:80px;background:var(--navy);display:flex;align-items:center;padding:0 30px;color:var(--white)}
.brand{display:flex;align-items:center;gap:8px;font-size:24px;font-weight:700;color:var(--white);margin-right:44px}
.brand-dot{width:12px;height:12px;border-radius:50%;background:var(--green)}
.main-nav{display:flex;gap:34px;font-size:14px;font-weight:500}
.main-nav span.drop::after{content:"";display:inline-block;width:5px;height:5px;border-right:1.5px solid #fff;border-bottom:1.5px solid #fff;transform:rotate(45deg);margin:0 0 3px 8px}
.header-actions{margin-left:auto;display:flex;align-items:center;gap:26px;font-size:14px;font-weight:500}
.header-actions .btn{width:94px;height:38px;font-size:14px}

/* Hero */
.hero{position:relative;height:468px;overflow:hidden}
.hero-photo{position:absolute;inset:0;background:
  linear-gradient(90deg,rgba(10,24,40,.55) 0%,rgba(10,24,40,.25) 45%,rgba(0,0,0,0) 70%),
  linear-gradient(180deg,#6d8193 0%,#4d6474 30%,#3a5a55 55%,#5a6b3c 80%,#36402a 100%)}
.hero-inner{position:relative;padding:98px 0 0 97px;color:var(--white)}
.hero h1{font-size:58px;line-height:1.0;font-weight:700;letter-spacing:-.5px}
.hero p{font-size:22px;line-height:1.38;margin-top:16px;width:470px}
.search-bar{position:absolute;left:97px;top:348px;width:846px;height:60px;background:var(--white);border-radius:6px;display:flex;align-items:center;padding:0 10px;gap:10px;box-shadow:0 4px 16px rgba(0,0,0,.2)}
.field{height:40px;border:1px solid var(--line);border-radius:4px;display:flex;align-items:center;gap:10px;padding:0 14px;font-size:12px;color:var(--soft)}
.field svg{flex:none}
.field.location{width:220px}
.field.dates{width:278px;color:var(--ink)}
.field.dates .arrow{margin:0 8px 0 auto;color:var(--soft)}
.field.guests{width:162px}
.field.guests .chev{margin-left:auto}
.search-bar .btn{width:128px;height:40px;font-size:14px}

/* Features */
.features{display:flex;padding:33px 0 0 92px;height:150px}
.feature{display:flex;gap:14px;width:257px}
.feature-icon{width:40px;height:40px;border:1px solid var(--line);border-radius:50%;display:flex;align-items:center;justify-content:center;flex:none;margin-top:6px}
.feature h3{font-size:14px;font-weight:700;color:var(--navy);margin-bottom:6px}
.feature p{font-size:11.5px;color:var(--muted);line-height:1.75;width:185px}

/* Fleet */
.fleet{text-align:center;height:735px}
.section-title{font-size:30px;font-weight:700;color:var(--navy);letter-spacing:-.2px}
.fleet .section-title{padding-top:2px}
.category-tabs{display:flex;justify-content:center;gap:0;margin-top:26px;padding-left:0}
.tab{width:122px;display:flex;flex-direction:column;align-items:center;gap:12px;font-size:13.5px;color:var(--muted);padding-bottom:10px}
.tab.active{color:var(--navy);font-weight:600;border-bottom:2px solid var(--green);width:74px;margin:0 24px}
.rv-grid{display:flex;gap:16px;justify-content:center;margin-top:26px}
.rv-card{width:240px;height:316px;border-radius:7px;background:var(--white);box-shadow:0 2px 10px rgba(15,30,58,.12);overflow:hidden;text-align:left;position:relative}
.rv-photo{height:187px}
.heart{position:absolute;top:10px;right:10px}
.rv-body{padding:13px 14px 0}
.rv-body h3{font-size:15px;font-weight:600;line-height:1.33;color:var(--ink);height:40px}
.rv-meta{display:flex;justify-content:space-between;font-size:11.5px;color:var(--soft);margin-top:8px}
.rv-meta .rating::before{content:"★";color:var(--star);margin-right:4px}
.rv-price{display:flex;justify-content:space-between;align-items:baseline;margin-top:12px}
.rv-price strong{font-size:22px;font-weight:700;color:var(--navy)}
.rv-price span{font-size:12px;color:var(--soft)}
.fleet .btn{width:181px;height:40px;margin-top:26px}

/* Earn */
.earn{background:var(--tint);height:338px;position:relative}
.earn-copy{position:absolute;left:107px;top:40px}
.earn h2{font-size:30px;font-weight:700;color:var(--navy)}
.earn-copy>p{font-size:15px;color:var(--muted);line-height:1.65;margin-top:12px;width:430px}
.checklist{list-style:none;margin-top:16px}
.checklist li{display:flex;align-items:center;gap:10px;font-size:14.5px;font-weight:500;color:var(--ink);margin-bottom:12px}
.earn .btn{width:176px;height:40px;margin-top:10px}
.earn-photo{position:absolute;left:601px;top:17px;width:513px;height:307px;border-radius:4px;background:linear-gradient(180deg,#8fa6bd 0%,#6f7d78 30%,#3f5a3e 55%,#5a6a54 75%,#6b6355 100%)}

/* How it works */
.how{text-align:center;height:377px;padding-top:28px}
.how .sub{font-size:15px;color:var(--muted);margin-top:6px}
.steps{display:flex;justify-content:center;gap:0;margin-top:26px;position:relative}
.steps::before{content:"";position:absolute;top:39px;left:323px;right:335px;border-top:1.5px dashed #d3d7dc}
.step{width:310px;display:flex;flex-direction:column;align-items:center;position:relative}
.step-icon{width:78px;height:78px;border-radius:50%;background:var(--white);border:1px solid var(--line);box-shadow:0 2px 8px rgba(15,30,58,.08);display:flex;align-items:center;justify-content:center}
.step h3{font-size:16px;font-weight:600;color:var(--navy);margin-top:16px}
.step p{font-size:12px;color:var(--muted);line-height:1.7;margin-top:6px;width:170px}
.how .btn{width:181px;height:40px;margin-top:26px}

/* Destinations */
.destinations{background:var(--tint);height:268px;text-align:center;padding-top:28px}
.dest-grid{display:flex;gap:15px;justify-content:center;margin-top:14px;padding-right:6px}
.dest{width:190px;height:163px;border-radius:5px;position:relative;overflow:hidden;text-align:left}
.dest-caption{position:absolute;left:12px;bottom:12px;color:var(--white);font-size:14.5px;font-weight:600;line-height:1.35}
.dest::after{content:"";position:absolute;inset:0;background:linear-gradient(180deg,rgba(0,0,0,0) 40%,rgba(0,0,0,.6) 100%)}
.dest-caption{z-index:1}

/* Testimonials */
.reviews{height:222px;text-align:center;padding-top:28px;background:#f7f9f8;margin-top:12px}
.reviews blockquote{font-size:15px;color:var(--muted);line-height:1.55;width:600px;margin:12px auto 0}
.reviewer{display:flex;justify-content:center;align-items:center;gap:12px;margin-top:10px;text-align:left;margin-left:-40px}
.avatar{width:40px;height:40px;border-radius:50%;background:linear-gradient(135deg,#b9a08a,#6f5646)}
.reviewer strong{display:block;font-size:14px;font-weight:600}
.reviewer span{font-size:13px;color:var(--muted)}
.dots{display:flex;justify-content:center;gap:11px;margin-top:18px}
.dots i{width:8px;height:8px;border-radius:50%;background:#c5cad1}
.dots i:first-child{background:var(--green)}

/* CTA */
.cta{position:relative;height:210px;text-align:center;color:var(--white)}
.cta-photo{position:absolute;inset:0;background:linear-gradient(90deg,#1e2d28 0%,#2c3b30 40%,#4a5351 75%,#2e3530 100%)}
.cta-photo::after{content:"";position:absolute;inset:0;background:rgba(10,20,30,.35)}
.cta-inner{position:relative;padding-top:30px}
.cta h2{font-size:30px;font-weight:700}
.cta p{font-size:15px;margin-top:16px}
.cta-actions{display:flex;justify-content:center;gap:27px;margin-top:22px}
.cta .btn{width:171px;height:40px;font-size:14px}
.btn.outline{background:transparent;border:1.5px solid var(--white);width:178px}

/* Footer */
.site-footer{background:var(--navy);height:268px;position:relative;color:var(--white)}
.footer-brand{position:absolute;left:97px;top:40px;width:200px}
.footer-brand .brand{font-size:26px;margin:0}
.footer-brand p{font-size:11px;line-height:1.8;color:#d6dbe4;margin-top:16px}
.socials{display:flex;gap:20px;margin-top:16px}
.socials i{width:16px;height:16px;border-radius:50%;border:1.6px solid var(--white)}
.footer-col{position:absolute;top:52px}
.footer-col h4{font-size:14px;font-weight:600;margin-bottom:10px}
.footer-col li{list-style:none;font-size:11px;color:#d6dbe4;margin-bottom:12px}
.footer-col p{font-size:11px;color:#d6dbe4}
.subscribe{display:flex;margin-top:14px;width:222px;height:34px}
.subscribe span{flex:1;background:var(--white);color:var(--soft);font-size:11px;display:flex;align-items:center;padding-left:12px;border-radius:3px 0 0 3px}
.subscribe b{width:77px;background:var(--green);font-size:11px;font-weight:600;display:flex;align-items:center;justify-content:center;border-radius:0 3px 3px 0}
.copyright{position:absolute;bottom:14px;left:0;right:0;text-align:center;font-size:15px;color:#d6dbe4}
</style>
</head>
<body>

<header class="site-header">
  <a class="brand"><span class="brand-dot"></span>Kelbrava.com</a>
  <nav class="main-nav">
    <a>How It Works</a><a>Find an RV</a><a>List Your RV</a><span class="drop">Resources</span><a>Support</a>
  </nav>
  <div class="header-actions"><a>Log In</a><a class="btn">Sign Up</a></div>
</header>

<section class="hero">
  <div class="hero-photo" role="img" aria-label="Motorhome with bikes parked beside a mountain lake among pine trees"></div>
  <div class="hero-inner">
    <h1>The Smart Way<br>to Rent an RV</h1>
    <p>Rent from local RV owners and explore the outdoors your way.</p>
  </div>
  <form class="search-bar">
    <div class="field location">
      <svg width="12" height="14" viewBox="0 0 12 14" fill="none" stroke="#15223b" stroke-width="1.4"><path d="M6 13s4.5-4.2 4.5-7.5a4.5 4.5 0 0 0-9 0C1.5 8.8 6 13 6 13z"/><circle cx="6" cy="5.5" r="1.6"/></svg>
      Enter location
    </div>
    <div class="field dates">
      <svg width="13" height="13" viewBox="0 0 13 13" fill="none" stroke="#15223b" stroke-width="1.3"><rect x="1" y="2" width="11" height="10" rx="1.5"/><path d="M1 5h11M4 1v2M9 1v2"/></svg>
      Pick up <span class="arrow">→</span>
      <svg width="13" height="13" viewBox="0 0 13 13" fill="none" stroke="#15223b" stroke-width="1.3"><rect x="1" y="2" width="11" height="10" rx="1.5"/><path d="M1 5h11M4 1v2M9 1v2"/></svg>
      Drop off
    </div>
    <div class="field guests">
      <svg width="13" height="13" viewBox="0 0 13 13" fill="none" stroke="#15223b" stroke-width="1.3"><circle cx="6.5" cy="4" r="2.8"/><path d="M1.2 12.5c.6-3 2.7-4.4 5.3-4.4s4.7 1.4 5.3 4.4"/></svg>
      Guests
      <svg class="chev" width="9" height="6" viewBox="0 0 9 6" fill="none" stroke="#8a919c" stroke-width="1.3"><path d="M1 1l3.5 3.5L8 1"/></svg>
    </div>
    <a class="btn">Search</a>
  </form>
</section>

<section class="features">
  <div class="feature">
    <div class="feature-icon"><svg width="18" height="18" viewBox="0 0 18 18" fill="none" stroke="#15223b" stroke-width="1.4"><path d="M9 2l6 3.5v7L9 16l-6-3.5v-7z"/><path d="M9 9v7M3 5.5L9 9l6-3.5"/></svg></div>
    <div><h3>Huge Selection</h3><p>Choose from thousands of RVs across the country.</p></div>
  </div>
  <div class="feature">
    <div class="feature-icon"><svg width="18" height="18" viewBox="0 0 18 18" fill="none" stroke="#15223b" stroke-width="1.4"><path d="M9 2v14M12.5 5.5c-.6-1.2-1.9-1.8-3.5-1.8-2 0-3.3 1-3.3 2.5 0 3.4 7 1.8 7 5.4 0 1.5-1.5 2.6-3.7 2.6-1.7 0-3.1-.7-3.7-2"/></svg></div>
    <div><h3>Affordable Prices</h3><p>Rent directly from owners and save big.</p></div>
  </div>
  <div class="feature">
    <div class="feature-icon"><svg width="18" height="18" viewBox="0 0 18 18" fill="none" stroke="#15223b" stroke-width="1.4"><path d="M9 1.5l6 2.3v4.6c0 3.7-2.5 6.6-6 8-3.5-1.4-6-4.3-6-8V3.8z"/><path d="M6 9l2.2 2.2L12.2 7"/></svg></div>
    <div><h3>Secure &amp; Simple</h3><p>Book with confidence through our secure platform.</p></div>
  </div>
  <div class="feature">
    <div class="feature-icon"><svg width="18" height="18" viewBox="0 0 18 18" fill="none" stroke="#15223b" stroke-width="1.4"><circle cx="9" cy="9" r="7"/><path d="M9 5v4l2.6 1.8"/></svg></div>
    <div><h3>24/7 Support</h3><p>We're here to help before, during, and after your trip.</p></div>
  </div>
</section>

<section class="fleet">
  <h2 class="section-title">Find the Perfect RV for Your Adventure</h2>
  <div class="category-tabs">
    <div class="tab active"><svg width="48" height="24" viewBox="0 0 48 24" fill="none" stroke="#15223b" stroke-width="1.4"><path d="M3 4h34l6 7v8H3z"/><path d="M8 8h7v5H8zM20 8h10v5H20z"/><circle cx="12" cy="19.5" r="2.5" fill="#fff"/><circle cx="34" cy="19.5" r="2.5" fill="#fff"/></svg>All RVs</div>
    <div class="tab"><svg width="48" height="24" viewBox="0 0 48 24" fill="none" stroke="#15223b" stroke-width="1.4"><path d="M4 5h30l8 6v8H4z"/><path d="M9 9h7v4H9zM20 9h8v4h-8z"/><circle cx="12" cy="19.5" r="2.5" fill="#fff"/><circle cx="34" cy="19.5" r="2.5" fill="#fff"/></svg>Drivables</div>
    <div class="tab"><svg width="48" height="24" viewBox="0 0 48 24" fill="none" stroke="#15223b" stroke-width="1.4"><path d="M4 4h34v14H4zM38 15h7"/><path d="M9 8h8v5H9zM22 8h10v5H22z"/><circle cx="20" cy="19.5" r="2.5" fill="#fff"/></svg>Towables</div>
    <div class="tab"><svg width="48" height="24" viewBox="0 0 48 24" fill="none" stroke="#15223b" stroke-width="1.4"><path d="M3 4h40v15H3z"/><path d="M7 8h6v5H7zM17 8h14v5H17zM35 8h5v5h-5z"/><circle cx="11" cy="19.5" r="2.5" fill="#fff"/><circle cx="35" cy="19.5" r="2.5" fill="#fff"/></svg>Class A</div>
    <div class="tab"><svg width="48" height="24" viewBox="0 0 48 24" fill="none" stroke="#15223b" stroke-width="1.4"><path d="M4 6h30l8 5v8H4z"/><path d="M9 10h8v4H9zM21 10h9v4h-9z"/><circle cx="12" cy="19.5" r="2.5" fill="#fff"/><circle cx="34" cy="19.5" r="2.5" fill="#fff"/></svg>Class B</div>
    <div class="tab"><svg width="48" height="24" viewBox="0 0 48 24" fill="none" stroke="#15223b" stroke-width="1.4"><path d="M3 4h30v4h5l6 5v6H3z"/><path d="M8 9h7v4H8zM19 9h9v4h-9z"/><circle cx="11" cy="19.5" r="2.5" fill="#fff"/><circle cx="35" cy="19.5" r="2.5" fill="#fff"/></svg>Class C</div>
    <div class="tab"><svg width="48" height="24" viewBox="0 0 48 24" fill="none" stroke="#15223b" stroke-width="1.4"><path d="M4 7h8V3h28v8h4v7H4z"/><path d="M16 7h8v5h-8zM28 7h8v5h-8z"/><circle cx="12" cy="19.5" r="2.5" fill="#fff"/><circle cx="18" cy="19.5" r="2.5" fill="#fff"/></svg>Fifth Wheels</div>
    <div class="tab"><svg width="48" height="24" viewBox="0 0 48 24" fill="none" stroke="#15223b" stroke-width="1.4"><path d="M5 4h32c3 0 5 3 5 6v8H5z"/><path d="M10 8h8v5h-8zM23 8h12v5H23z"/><circle cx="22" cy="19.5" r="2.5" fill="#fff"/><circle cx="28" cy="19.5" r="2.5" fill="#fff"/></svg>Travel Trailers</div>
  </div>

  <div class="rv-grid">
    <article class="rv-card">
      <div class="rv-photo" role="img" aria-label="White Class C motorhome parked under a blue sky" style="background:linear-gradient(180deg,#5d90c9 0%,#a9c3de 45%,#e8eaec 60%,#8d9691 100%)"></div>
      <svg class="heart" width="20" height="18" viewBox="0 0 20 18" fill="none" stroke="#fff" stroke-width="1.6"><path d="M10 16S2 11 2 6a4 4 0 0 1 8-1.3A4 4 0 0 1 18 6c0 5-8 10-8 10z"/></svg>
      <div class="rv-body">
        <h3>2021 Ridgeline Coach Summit K24</h3>
        <div class="rv-meta"><span>Denver, CO</span><span class="rating">4.9 (32)</span></div>
        <div class="rv-price"><strong>$175</strong><span>/night</span></div>
      </div>
    </article>
    <article class="rv-card">
      <div class="rv-photo" role="img" aria-label="Travel trailer parked at a shaded campsite" style="background:linear-gradient(180deg,#4f6a3b 0%,#7c8f68 35%,#d9dad6 55%,#8e8c83 100%)"></div>
      <svg class="heart" width="20" height="18" viewBox="0 0 20 18" fill="none" stroke="#fff" stroke-width="1.6"><path d="M10 16S2 11 2 6a4 4 0 0 1 8-1.3A4 4 0 0 1 18 6c0 5-8 10-8 10z"/></svg>
      <div class="rv-body">
        <h3>2019 Pinecrest Trailway 27BH</h3>
        <div class="rv-meta"><span>Nashville, TN</span><span class="rating">4.8 (18)</span></div>
        <div class="rv-price"><strong>$120</strong><span>/night</span></div>
      </div>
    </article>
    <article class="rv-card">
      <div class="rv-photo" role="img" aria-label="Silver camper van on a forest road" style="background:linear-gradient(180deg,#a9bccb 0%,#5f7460 35%,#8b9397 60%,#6e7466 100%)"></div>
      <svg class="heart" width="20" height="18" viewBox="0 0 20 18" fill="none" stroke="#fff" stroke-width="1.6"><path d="M10 16S2 11 2 6a4 4 0 0 1 8-1.3A4 4 0 0 1 18 6c0 5-8 10-8 10z"/></svg>
      <div class="rv-body">
        <h3>2022 Marlow Voyager 59V</h3>
        <div class="rv-meta"><span>Austin, TX</span><span class="rating">5.0 (24)</span></div>
        <div class="rv-price"><strong>$200</strong><span>/night</span></div>
      </div>
    </article>
    <article class="rv-card">
      <div class="rv-photo" role="img" aria-label="Black and white travel trailer by a lake" style="background:linear-gradient(180deg,#7f9fbf 0%,#48604d 35%,#d2d4d4 55%,#3c3f43 80%,#6f6c62 100%)"></div>
      <svg class="heart" width="20" height="18" viewBox="0 0 20 18" fill="none" stroke="#fff" stroke-width="1.6"><path d="M10 16S2 11 2 6a4 4 0 0 1 8-1.3A4 4 0 0 1 18 6c0 5-8 10-8 10z"/></svg>
      <div class="rv-body">
        <h3>2020 Northfield Horizon 2800BH</h3>
        <div class="rv-meta"><span>Seattle, WA</span><span class="rating">4.9 (15)</span></div>
        <div class="rv-price"><strong>$150</strong><span>/night</span></div>
      </div>
    </article>
  </div>
  <a class="btn">View All RVs</a>
</section>

<section class="earn">
  <div class="earn-copy">
    <h2>Earn More. Keep More.</h2>
    <p>List your RV on Kelbrava.com and keep all your earnings. We charge one flat monthly rate with no hidden fees.</p>
    <ul class="checklist">
      <li><svg width="16" height="16" viewBox="0 0 16 16" fill="none" stroke="#4b7d22" stroke-width="1.8"><circle cx="8" cy="8" r="6.8"/><path d="M5 8.2l2 2 4-4"/></svg>Keep 100% of your rental earnings</li>
      <li><svg width="16" height="16" viewBox="0 0 16 16" fill="none" stroke="#4b7d22" stroke-width="1.8"><circle cx="8" cy="8" r="6.8"/><path d="M5 8.2l2 2 4-4"/></svg>One simple monthly rate</li>
      <li><svg width="16" height="16" viewBox="0 0 16 16" fill="none" stroke="#4b7d22" stroke-width="1.8"><circle cx="8" cy="8" r="6.8"/><path d="M5 8.2l2 2 4-4"/></svg>Support from a team that cares</li>
    </ul>
    <a class="btn">List Your RV</a>
  </div>
  <div class="earn-photo" role="img" aria-label="Motorhome parked at a lakeside campsite with chairs and a campfire beneath mountains"></div>
</section>

<section class="how">
  <h2 class="section-title">How It Works</h2>
  <p class="sub">Renting an RV has never been easier.</p>
  <div class="steps">
    <div class="step">
      <div class="step-icon"><svg width="30" height="26" viewBox="0 0 30 26" fill="#15223b"><path d="M2 6h16l4 5v8H2z"/><circle cx="7" cy="20" r="2.5"/><circle cx="17" cy="20" r="2.5"/><circle cx="23" cy="14" r="4.5" fill="#fff" stroke="#15223b" stroke-width="2"/><path d="M26 17l3 3" stroke="#15223b" stroke-width="2"/></svg></div>
      <h3>Search</h3>
      <p>Find the perfect RV for your trip and send a request.</p>
    </div>
    <div class="step">
      <div class="step-icon"><svg width="30" height="28" viewBox="0 0 30 28" fill="none" stroke="#15223b" stroke-width="2"><rect x="3" y="4" width="18" height="17" rx="2"/><path d="M3 9h18M8 2v4M16 2v4"/><circle cx="20" cy="18" r="5" fill="#fff"/><path d="M24 22l3 3"/></svg></div>
      <h3>Book</h3>
      <p>Connect with the owner, finalize the details, and book with confidence.</p>
    </div>
    <div class="step">
      <div class="step-icon"><svg width="28" height="26" viewBox="0 0 28 26" fill="#15223b"><rect x="5" y="3" width="16" height="15" rx="1.5"/><path d="M2 21h24v2H2z"/><rect x="9" y="7" width="8" height="5" fill="#fff"/></svg></div>
      <h3>Hit the Road</h3>
      <p>Pick up your RV and enjoy your adventure!</p>
    </div>
  </div>
  <a class="btn">Learn More</a>
</section>

<section class="destinations">
  <h2 class="section-title" style="font-size:26px">Popular Destinations</h2>
  <div class="dest-grid">
    <div class="dest" role="img" aria-label="Mountain valley with a river and autumn forest" style="background:linear-gradient(180deg,#9db8d2 0%,#6b8a6f 40%,#a2873e 70%,#3e4a33 100%)"><div class="dest-caption">Yellowstone<br>National Park</div></div>
    <div class="dest" role="img" aria-label="Red canyon walls and layered rock" style="background:linear-gradient(180deg,#b3867a 0%,#9c5b48 40%,#6e3a2f 75%,#3b2520 100%)"><div class="dest-caption">Grand Canyon<br>Arizona</div></div>
    <div class="dest" role="img" aria-label="Forested green mountain ridges with a lake" style="background:linear-gradient(180deg,#c8c6a6 0%,#6e8a4c 40%,#4b6a3a 70%,#2f3f29 100%)"><div class="dest-caption">Great Smoky Mountains<br>Tennessee</div></div>
    <div class="dest" role="img" aria-label="Red sandstone cliffs above a green valley" style="background:linear-gradient(180deg,#9cc0db 0%,#b5613d 40%,#7d6a3a 70%,#3d3a28 100%)"><div class="dest-caption">Zion National Park<br>Utah</div></div>
    <div class="dest" role="img" aria-label="Coastal lake and hills under a blue sky" style="background:linear-gradient(180deg,#7fa6cc 0%,#8ba0a8 40%,#4f6a55 70%,#2d3a2f 100%)"><div class="dest-caption">Acadia National Park<br>Maine</div></div>
  </div>
</section>

<section class="reviews">
  <h2 class="section-title" style="font-size:26px">What RVers Are Saying</h2>
  <blockquote>"Kelbrava.com made our trip amazing! The RV was perfect and the owner was great to work with. We'll definitely rent again!"</blockquote>
  <div class="reviewer">
    <div class="avatar" role="img" aria-label="Reviewer portrait"></div>
    <div><strong>Dana M.</strong><span>Orlando, FL</span></div>
  </div>
  <div class="dots"><i></i><i></i><i></i><i></i></div>
</section>

<section class="cta">
  <div class="cta-photo" role="img" aria-label="Motorhome on a forest road at dusk"></div>
  <div class="cta-inner">
    <h2>Start Your Adventure Today</h2>
    <p>Join thousands of happy RV renters and owners.</p>
    <div class="cta-actions"><a class="btn">Find an RV</a><a class="btn outline">List Your RV</a></div>
  </div>
</section>

<footer class="site-footer">
  <div class="footer-brand">
    <a class="brand"><span class="brand-dot"></span>Kelbrava.com</a>
    <p>The peer-to-peer RV rental marketplace where owners earn more and renters adventure more.</p>
    <div class="socials"><i></i><i></i><i></i></div>
  </div>
  <div class="footer-col" style="left:341px"><h4>Explore</h4><ul><li>Find an RV</li><li>List Your RV</li><li>How It Works</li><li>Destinations</li></ul></div>
  <div class="footer-col" style="left:518px"><h4>Support</h4><ul><li>Help Center</li><li>Safety</li><li>Terms of Service</li><li>Privacy Policy</li></ul></div>
  <div class="footer-col" style="left:696px"><h4>Company</h4><ul><li>About Us</li><li>Careers</li><li>Contact Us</li><li>Blog</li></ul></div>
  <div class="footer-col" style="left:865px"><h4>Stay Connected</h4><p>Get tips, ideas, and RV deals.</p>
    <div class="subscribe"><span>Enter your email</span><b>Subscribe</b></div>
  </div>
  <p class="copyright">© 2026 kelbrava.com, All rights reserved.</p>
</footer>

</body>
</html>
```